A 'new law' boutique Australian law firm that provides specialist employment law and people managem

We value helping clients create results with respect workplaces. What differentiates us is we provide actionable training in understanding and dealing with people and ensure legal compliance fits with this approach. We would like a fresh approach to our training overview documents that we currently use in our current law firm (6 attached). Please use pictures, symbols etc consistent with our non-traditional law approach that captures the approach of each training session.. Attached is the logo and draft letterhead for Birchwell Legal which will launch soon.

Target Market(s)

HR Managers and in-house lawyers (non employment specialists) in mid-large Australian companies that are progressive with a relationship based approach to managing employee behaviours and disputes.

Industry/Entity Type

Human Resource

Font styles to use
Sans Serif

Colors
3176b5
33a6d7

Requirements
Must have
• 1 or 2 page PDF for each of the 6 documents that the wording supplied goes into your design which will be pretty similar as we want consistency with our documents

```html
<!DOCTYPE html>
<html lang="en">
<head>
<meta charset="utf-8">
<title>Contact Officer Training – Birchwell Legal</title>
<link rel="stylesheet" href="https://fonts.googleapis.com/css2?family=Merriweather:wght@300;400;700&display=swap">
<style>
  :root {
    --ink: #232323;
    --ink-soft: #2c2c2c;
    --paper: #ffffff;
    --blue-deep: #3176b5;
    --blue: #33a6d7;
    --blue-mid: #5bbdea;
    --blue-light: #8ad2f3;
    --blue-pale: #e2f3fc;
    --text-dark: #1d2a36;
    --text-on-dark: #e9e9e9;
    --backdrop: #d6d6d6;
  }
  * { box-sizing: border-box; margin: 0; padding: 0; }
  html, body { width: 1200px; height: 800px; overflow: hidden; }
  body {
    background: var(--backdrop);
    font-family: "Merriweather", Georgia, serif;
    display: flex; align-items: center; justify-content: center;
  }
  .flyer {
    width: 1120px; height: 740px;
    display: grid;
    grid-template-columns: 420px 1fr;
    background: var(--paper);
    box-shadow: 0 10px 30px rgba(0,0,0,.25);
  }
  .intro-panel {
    background: var(--ink);
    color: var(--text-on-dark);
    padding: 44px 40px;
    display: flex; flex-direction: column;
  }
  .brand { display: flex; align-items: center; gap: 12px; margin-bottom: 56px; }
  .brand-dot { width: 30px; height: 30px; border-radius: 50%; background: var(--blue); }
  .brand-name { font-size: 24px; font-weight: 400; color: var(--blue); letter-spacing: .5px; }
  .title { font-size: 34px; font-weight: 700; line-height: 1.15; color: #fff; }
  .title .accent { display: block; color: var(--blue); }
  .subtitle { font-size: 19px; color: var(--blue); margin: 18px 0 16px; font-weight: 400; }
  .intro-panel p { font-size: 12.5px; line-height: 1.65; font-weight: 300; margin-bottom: 14px; }

  .detail { display: grid; grid-template-rows: auto 1fr; }
  .overview {
    background: var(--blue);
    display: grid; grid-template-columns: repeat(4, 1fr);
  }
  .overview-head {
    grid-column: 1 / -1;
    padding: 18px 26px 10px;
    font-size: 20px; font-weight: 700; color: var(--blue-deep);
  }
  .topic { padding: 12px 18px 16px; color: var(--text-dark); min-height: 170px; }
  .topic h3 { font-size: 13.5px; font-weight: 700; margin-bottom: 6px; }
  .topic p { font-size: 10.5px; line-height: 1.5; }
  .topic:nth-of-type(4n+1) { background: var(--blue); }
  .topic:nth-of-type(4n+2) { background: var(--blue-light); }
  .topic:nth-of-type(4n+3) { background: var(--blue-pale); }
  .topic:nth-of-type(4n+4) { background: var(--blue-mid); }
  .topic:nth-of-type(n+6) { }

  .outcomes { position: relative; padding: 34px 40px 30px 170px; color: var(--text-dark); }
  .outcomes-icon {
    position: absolute; left: 40px; top: 30px;
    width: 104px; height: 104px; border-radius: 50%;
    background: var(--paper); border: 5px solid #555;
    display: flex; align-items: center; justify-content: center;
  }
  .outcomes h2 { font-size: 22px; color: var(--blue-deep); font-weight: 700; margin-bottom: 8px; }
  .outcomes .lead { font-size: 13px; font-weight: 700; margin-bottom: 8px; }
  .outcomes ol { font-size: 13px; line-height: 1.7; padding-left: 20px; }
</style>
</head>
<body>
  <article class="flyer">
    <section class="intro-panel">
      <div class="brand"><span class="brand-dot"></span><span class="brand-name">Birchwell Legal</span></div>
      <h1 class="title">Contact <span class="accent">Officer Training</span></h1>
      <h2 class="subtitle">Training Need</h2>
      <p>Unlawful or inappropriate behaviour in the workplace that is left unaddressed can impact on productivity and employee retention. Claims can be costly in terms of time and money as well as the impact on mental health from being involved in an adversarial process.</p>
      <p>Clear policies and procedures explaining the organisation's workplace behaviour expectations and how grievances will be managed are a minimum compliance requirement.</p>
      <p>The challenge is ensuring that employees understand the directions contained in those policies, what is unlawful and inappropriate behaviour and the options available to address those behaviours if they experience them or engage in them.</p>
      <p>Well trained Contact Officers provide another resource to assist the organisation to provide a safe and respectful workplace.</p>
    </section>

    <section class="detail">
      <div class="overview">
        <h2 class="overview-head">Training Overview</h2>
        <div class="topic"><h3>Discrimination</h3><p>What is direct and indirect discrimination? What are the protected attributes? What are the exemptions to the general rule? Practical examples of behaviour that may be discriminatory.</p></div>
        <div class="topic"><h3>Harassment</h3><p>What is harassment? What is sexual harassment? What is the difference between harassment and bullying? Practical examples of behaviour that may be harassment.</p></div>
        <div class="topic"><h3>Bullying</h3><p>What is bullying? Explore how bullying differs to discrimination or inappropriate behaviour. Is all workplace conflict bullying? Practical examples of behaviour that may be bullying.</p></div>
        <div class="topic"><h3>Victimisation &amp; Vilification</h3><p>What is victimisation? What is vilification? How do they arise at work?</p></div>
        <div class="topic"><h3>Adverse Action</h3><p>What is adverse action and how does it differ to other unlawful behaviour? What is a workplace right? How can the protections affect a response to adverse action?</p></div>
        <div class="topic"><h3>The Contact Officer's role</h3><p>How to perform your role when approached by an employee. What are the limits? What are the obligations with respect to confidentiality?</p></div>
        <div class="topic"><h3>Grievance Options</h3><p>Explore the options of informal resolution, formal internal investigation and external avenues. The advantages and disadvantages of each approach.</p></div>
        <div class="topic"><h3>Test Learning</h3><p>Role plays and group discussion.</p></div>
      </div>

      <div class="outcomes">
        <div class="outcomes-icon">
          <svg width="80" height="80" viewBox="0 0 80 80" role="img" aria-label="Icon of a trainer presenting to a small group">
            <circle cx="40" cy="40" r="38" fill="#33a6d7"/>
          </svg>
        </div>
        <h2>Learning Outcomes</h2>
        <p class="lead">Training will enable participants to perform their role of Contact Officer and to understand:</p>
        <ol>
          <li>The role and responsibilities of a Contact Officer.</li>
          <li>What amounts to unlawful workplace behaviour.</li>
          <li>What is considered inappropriate behaviour in our workplace.</li>
          <li>How to apply understanding unlawful/inappropriate behaviour to common scenarios.</li>
          <li>How to address and resolve grievances early.</li>
          <li>Options to resolve grievances internally and the Contact Officer role.</li>
          <li>External options and their pros and cons for resolving grievances.</li>
        </ol>
      </div>
    </section>
  </article>
</body>
</html>
```